MS Word Template for Proposals and RFP

Looking for a nice looking graphic template in MS Word. We will use this to make proposals and answer RFPs. Looking for something that will match our company brand, but give a fresh, up-to-date look and feel. There are a few pictures of a template I like. I don't necessarily like that logo - looks too "kid like" for business, but I really like how clean and organized it is. Most proposals and RFP responses are looooooonnnngggg and boring - need something that someone can look through and find what they are looking for quickly and easily.
Updates

Can't wait to see your designs!

Target Market(s)

School districts and other governmental employers

Industry/Entity Type

Business

Requirements
Must have
• Must include sample table of contents, section dividers, charts, graphs and tables that we customized based on the content. The goal is for it to look simple, clean, compelling - organized so it's easy to read, easy to find your way around - good headers, charts, flow charts, tables.... etc. Looking to have 5-10 template pages that we can use to put together and entire portfolio.
Should not have
• No "cutsie" comic sans/apple for the teacher kind of stuff - we are selling employee benefits to schools and other governmental entities. Should be more serious and conservative but also look compelling and draw in the reader.

```html
<!DOCTYPE html>
<html lang="en">
<head>
<meta charset="utf-8">
<title>Table Data — Proposal Template</title>
<link rel="stylesheet" href="https://fonts.googleapis.com/css2?family=Arimo:wght@400;700&display=swap">
<style>
  :root {
    --brand-blue: #5a7fc6;
    --brand-navy: #2f4f8f;
    --brand-deep: #1f3a70;
    --title-blue: #3f6fc0;
    --body-text: #4a4a4a;
    --row-gray: #f1f1f2;
    --row-blue: #e2e9f5;
    --cell-text: #5a5a5a;
    --white: #ffffff;
  }
  * { box-sizing: border-box; margin: 0; padding: 0; }
  html, body { width: 900px; height: 1200px; overflow: hidden; background: var(--white); }
  body { font-family: "Arimo", Arial, sans-serif; position: relative; }

  .page-header { position: absolute; top: 0; left: 0; width: 900px; height: 60px; }
  .page-header svg { position: absolute; inset: 0; }
  .section-label {
    position: absolute; right: 30px; top: 12px;
    color: var(--white); font-size: 31px; font-weight: 400;
  }

  .section-title {
    position: absolute; left: 30px; top: 92px;
    color: var(--title-blue); font-size: 33px; font-weight: 400;
  }
  .intro {
    position: absolute; left: 30px; top: 136px; width: 842px;
    color: var(--body-text); font-size: 19px; line-height: 33px;
    text-align: justify; hyphens: manual;
  }

  .data-table {
    position: absolute; left: 42px; top: 372px; width: 828px;
    border-collapse: collapse; font-size: 19px; table-layout: fixed;
  }
  .data-table th {
    background: var(--brand-blue); color: var(--white);
    font-weight: 400; height: 48px; text-align: left; white-space: nowrap;
  }
  .data-table .col-heading { width: 300px; }
  .data-table .col-mid { width: 190px; text-align: center; }
  .data-table th.col-end { padding-left: 18px; }
  .data-table td { height: 56px; color: var(--cell-text); white-space: nowrap; }
  .data-table tbody tr:nth-child(odd) td { background: var(--row-gray); }
  .data-table tbody tr:nth-child(even) td { background: var(--row-blue); }
  .data-table .row-heading { padding-left: 24px; }
  .data-table .value-mid { text-align: center; }
  .data-table .value-end { text-align: right; padding-right: 66px; }

  .page-footer { position: absolute; left: 0; bottom: 0; width: 900px; height: 75px; }
  .page-footer svg { position: absolute; inset: 0; }
  .company-name {
    position: absolute; left: 28px; top: 24px;
    color: var(--white); font-size: 21px; font-weight: 700; letter-spacing: 0.5px;
    display: flex; align-items: center; gap: 10px;
  }
  .company-name .mark { width: 14px; height: 14px; background: var(--white); }
  .company-url {
    position: absolute; right: 30px; top: 26px;
    color: var(--white); font-size: 20px;
  }
</style>
</head>
<body>
  <header class="page-header">
    <svg width="900" height="60" viewBox="0 0 900 60">
      <rect width="900" height="60" fill="var(--brand-blue)"/>
      <polygon points="0,0 150,0 95,60 0,60" fill="var(--brand-navy)"/>
      <polygon points="150,0 170,0 115,60 95,60" fill="var(--brand-deep)" opacity="0.5"/>
    </svg>
    <div class="section-label">Contents</div>
  </header>

  <h1 class="section-title">Table Data</h1>
  <p class="intro">This template uses a few tables to create the page structure that follows. A host table consisting of just two columns and one row enables the sidebar content to sit beside the text, tables, and dia&shy;gram on the left without any complicated positioning required. Nested tables (a nested table is just one table inside another) in both the left and right column enable you to place text beside the ProcessFlow graphic, provide the small financial table below left, and provide the sidebar table with a separate cell for the heading text.</p>

  <table class="data-table">
    <thead>
      <tr>
        <th class="col-heading"></th>
        <th class="col-mid">Table Text Centered</th>
        <th class="col-end">Table Text Centered</th>
      </tr>
    </thead>
    <tbody>
      <tr><td class="row-heading">TABLE ROW HEADING</td><td class="value-mid">000</td><td class="value-end">000</td></tr>
      <tr><td class="row-heading">TABLE ROW HEADING</td><td class="value-mid">000</td><td class="value-end">000</td></tr>
      <tr><td class="row-heading">TABLE ROW HEADING</td><td class="value-mid">000</td><td class="value-end">000</td></tr>
      <tr><td class="row-heading">TABLE ROW HEADING</td><td class="value-mid">000</td><td class="value-end">000</td></tr>
      <tr><td class="row-heading">TABLE ROW HEADING</td><td class="value-mid">000</td><td class="value-end">000</td></tr>
      <tr><td class="row-heading">TABLE ROW HEADING</td><td class="value-mid">000</td><td class="value-end">000</td></tr>
      <tr><td class="row-heading">TABLE ROW HEADING</td><td class="value-mid">000</td><td class="value-end">000</td></tr>
      <tr><td class="row-heading">TABLE ROW HEADING</td><td class="value-mid">000</td><td class="value-end">000</td></tr>
    </tbody>
  </table>

  <footer class="page-footer">
    <svg width="900" height="75" viewBox="0 0 900 75">
      <rect width="900" height="75" fill="var(--brand-blue)"/>
      <polygon points="0,0 330,0 300,75 0,75" fill="var(--brand-navy)"/>
    </svg>
    <div class="company-name"><span class="mark"></span>CRESTLINE BENEFIT SERVICES</div>
    <div class="company-url">www.CrestlineBenefits.com</div>
  </footer>
</body>
</html>
```